Simple and Clean business card design

We would like the design to be simple clean and to incorporate our colors.

We are open to your design and talent, we have the dots in our logo as we think of it as data points and we connect data points for people.

We are open to see the great creative and clean design you bring to the table

Contact Information for Business Card

please include: name, position, email, phone and website

Font styles to use
Sans Serif

Requirements
Must have
• my colors incorporated, simplicity
Nice to have
• lots of white space, simplicity
Should not have
• complexicity/ complex art

```html
<!DOCTYPE html>
<html lang="en">
<head>
<meta charset="utf-8">
<title>Nectra — Business Card</title>
<link rel="stylesheet" href="https://fonts.googleapis.com/css2?family=Open+Sans:wght@400;600&family=Saira:wght@500;600&display=swap">
<style>
  :root {
    --brand-blue: #4285f4;
    --ink: #111111;
    --paper: #ffffff;
    --faint-blue: #d9e1f2;
    --border: #222222;
    --rule-grey: #8a8a8a;
  }
  * { box-sizing: border-box; margin: 0; padding: 0; }
  html, body {
    width: 1200px;
    height: 1200px;
    overflow: hidden;
    background: var(--paper);
  }
  .canvas { position: relative; width: 1200px; height: 1200px; }

  .card {
    position: absolute;
    left: 216px;
    width: 775px;
    height: 430px;
    border: 1px solid var(--border);
    overflow: hidden;
  }
  .card--front { top: 147px; background: var(--brand-blue); }
  .card--back { top: 630px; background: var(--paper); }

  .wordmark {
    position: absolute;
    font-family: "Open Sans", sans-serif;
    font-weight: 600;
    line-height: 1;
    white-space: nowrap;
    letter-spacing: 1px;
  }

  /* Front */
  .front-rule {
    position: absolute;
    top: 214px;
    height: 2px;
    background: var(--paper);
  }
  .front-rule--left { left: 0; width: 193px; }
  .front-rule--right { left: 582px; right: 0; }
  .front-wordmark {
    left: 0; right: 0;
    top: 166px;
    text-align: center;
    font-size: 100px;
    color: var(--paper);
  }
  .front-web {
    position: absolute;
    left: 0; right: 0;
    top: 346px;
    display: flex;
    justify-content: center;
    align-items: center;
    gap: 26px;
    font-family: "Open Sans", sans-serif;
    font-size: 19px;
    color: var(--paper);
    letter-spacing: 0.3px;
  }
  .front-web .dot {
    width: 9px; height: 9px;
    border-radius: 50%;
    background: var(--paper);
  }

  /* Back */
  .back-logo {
    position: absolute;
    right: 18px;
    top: 44px;
    display: flex;
    align-items: flex-end;
    gap: 12px;
  }
  .back-logo .mark-dot {
    width: 22px; height: 22px;
    border-radius: 50%;
    background: var(--brand-blue);
    margin-bottom: 8px;
  }
  .back-logo .wordmark {
    position: static;
    font-size: 100px;
    color: var(--ink);
  }
  .back-watermark {
    right: 18px;
    top: 262px;
    font-size: 148px;
    color: var(--faint-blue);
  }

  .person-name {
    position: absolute;
    left: 26px;
    top: 184px;
    font-family: "Saira", sans-serif;
    font-weight: 600;
    font-size: 35px;
    line-height: 1;
    color: var(--brand-blue);
    letter-spacing: 0.5px;
  }
  .person-role {
    position: absolute;
    left: 26px;
    top: 220px;
    font-family: "Saira", sans-serif;
    font-weight: 600;
    font-size: 16px;
    line-height: 1;
    color: var(--ink);
    letter-spacing: 1.5px;
  }
  .role-rule {
    position: absolute;
    left: 131px;
    top: 229px;
    width: 610px;
    height: 1px;
    background: linear-gradient(to right, var(--ink), var(--rule-grey) 60%, rgba(255,255,255,0));
  }

  .contact-list {
    position: absolute;
    left: 28px;
    top: 263px;
    list-style: none;
  }
  .contact-item {
    display: flex;
    align-items: center;
    gap: 14px;
    height: 42px;
    margin-bottom: 8px;
    font-family: "Open Sans", sans-serif;
    font-size: 21px;
    color: var(--ink);
  }
  .contact-icon {
    width: 42px; height: 42px;
    border-radius: 50%;
    background: var(--brand-blue);
    display: flex;
    align-items: center;
    justify-content: center;
    flex: none;
  }
  .contact-icon svg { width: 24px; height: 24px; }
</style>
</head>
<body>
<main class="canvas">

  <section class="card card--front" aria-label="Card front">
    <div class="front-rule front-rule--left"></div>
    <div class="front-rule front-rule--right"></div>
    <div class="wordmark front-wordmark">Nectra</div>
    <div class="front-web">
      <span class="dot"></span>
      <span>www.nectra.one</span>
      <span class="dot"></span>
    </div>
  </section>

  <section class="card card--back" aria-label="Card back">
    <div class="wordmark back-watermark" aria-hidden="true">Nectra</div>

    <div class="back-logo">
      <span class="mark-dot"></span>
      <span class="wordmark">Nectra</span>
    </div>

    <h1 class="person-name">LENA MOSS</h1>
    <p class="person-role">FOUNDER</p>
    <div class="role-rule"></div>

    <ul class="contact-list">
      <li class="contact-item">
        <span class="contact-icon">
          <svg viewBox="0 0 24 24" fill="none" stroke="#fff" stroke-width="1.4">
            <rect x="7" y="2.5" width="10" height="19" rx="1.5"/>
            <line x1="10.5" y1="4.5" x2="13.5" y2="4.5"/>
            <circle cx="12" cy="19" r="0.6" fill="#fff"/>
          </svg>
        </span>
        <span>555-210-3846</span>
      </li>
      <li class="contact-item">
        <span class="contact-icon">
          <svg viewBox="0 0 24 24" fill="none" stroke="#fff" stroke-width="1.4">
            <rect x="3" y="6" width="18" height="12"/>
            <polyline points="3,6 12,13 21,6"/>
            <line x1="3" y1="18" x2="10" y2="11.5"/>
            <line x1="21" y1="18" x2="14" y2="11.5"/>
          </svg>
        </span>
        <span>www.nectra.one</span>
      </li>
      <li class="contact-item">
        <span class="contact-icon">
          <svg viewBox="0 0 24 24" fill="none" stroke="#fff" stroke-width="1.2">
            <circle cx="12" cy="12" r="9"/>
            <ellipse cx="12" cy="12" rx="4" ry="9"/>
            <line x1="12" y1="3" x2="12" y2="21"/>
            <line x1="3" y1="12" x2="21" y2="12"/>
            <path d="M4.5 7.5h15M4.5 16.5h15"/>
          </svg>
        </span>
        <span>lena.moss@nectra.one</span>
      </li>
    </ul>
  </section>

</main>
</body>
</html>
```